Design für Geburtskarte A6 hoch, Klappkarte
Zielgruppe
Ich bin Fotograf und habe mich auf Schwangerschafts- und Neugeborenenfotografie spezialisiert. Meine Zielgruppe sind schwangere Frauen im letzten Drittel der Schwangerschaft und frisch gewordene Eltern.
Aufgabenstellung
- sehr schlichtes Design, in der Anlage finden Sie zwei der meist verkauften Karten damit Sie sich vom Stil eine Vorstellung machen können
- Lieferung als offene Indesign 5.5 Datei (so das die Farben, Texte, .... angepasst werden können)
- 2-3 Bilder (querformat) sollen in das Design eingearbeitet werden können
- Die Karten werden von mir nachher als fertig gedruckte Karte an meine Kunden verkauft, dies bitte ich zu berücksichtigen
- ich möchte die Karten so nutzen können das sowohl Geburtskarten für Jungs wie auch für Mädels erstellt werden können
- Format: Din A6 (geschlossen 105x148mm), Klappkarte, hoch, 3mm Beschnitt

```html
<!DOCTYPE html>
<html lang="de">
<head>
<meta charset="utf-8">
<title>Geburtskarte Theo – Klappkarte A6</title>
<link rel="stylesheet" href="https://fonts.googleapis.com/css2?family=Caveat+Brush&family=Dancing+Script:wght@500&family=Crimson+Text&display=swap">
<style>
  :root{
    --page:#ffffff;
    --sheet-line:#cfcfcf;
    --blue-cover:#88a9b9;
    --blue-front:#7fa1b3;
    --blue-inside:#abc2cd;
    --teal-dark:#3f6a78;
    --frame:#ffffff;
    --ink-light:#ffffff;
    --photo-a:#c9d3d8;
    --photo-b:#e6d2c4;
  }
  *{box-sizing:border-box;margin:0;padding:0}
  html,body{width:848px;height:1200px;overflow:hidden;background:var(--page)}
  .canvas{position:relative;width:848px;height:1200px}
  .spread{position:absolute;left:50px;width:751px;height:530px;border:1px solid var(--sheet-line);background:var(--page)}
  .spread--outside{top:42px}
  .spread--inside{top:604px}
  .panel{position:absolute;top:10px;height:508px}
  .panel--back{left:10px;width:354px;background:var(--blue-cover)}
  .panel--front{left:387px;width:354px;background:var(--blue-front)}
  .panel--inside{left:10px;width:731px;background:var(--blue-inside)}
  .fold{position:absolute;top:0;bottom:0;left:375px;width:1px;background:#e3e3e3}
  .fold--inside{background:rgba(255,255,255,.35);top:10px;bottom:10px}

  .photo{position:absolute;background:var(--frame);padding:10px;box-shadow:0 2px 5px rgba(0,0,0,.22)}
  .photo__image{width:100%;height:100%;background:linear-gradient(135deg,var(--photo-a),var(--photo-b))}
  .photo::before,.photo::after{content:"";position:absolute;width:40px;height:40px;background:rgba(255,255,255,.55)}
  .photo::before{left:-4px;top:-4px;clip-path:polygon(0 0,100% 0,0 100%)}
  .photo::after{right:-4px;bottom:-4px;clip-path:polygon(100% 0,100% 100%,0 100%)}

  .photo--cover{left:24px;top:60px;width:323px;height:228px}
  .photo--inside-left{left:32px;top:234px;width:324px;height:227px}
  .photo--inside-top{left:400px;top:25px;width:324px;height:227px}
  .photo--inside-bottom{left:401px;top:268px;width:330px;height:228px;transform:rotate(-1.6deg)}

  .badge{position:absolute;left:-13px;top:57px;width:380px;height:254px}
  .name{position:absolute;left:0;width:100%;top:318px;text-align:center;font-family:"Caveat Brush",cursive;font-size:64px;line-height:1;color:var(--ink-light);text-shadow:0 2px 3px rgba(0,0,0,.25)}
  .facts{position:absolute;left:0;width:100%;top:392px;text-align:center;font-family:"Dancing Script",cursive;font-size:22px;line-height:28px;color:var(--ink-light);text-shadow:0 1px 2px rgba(0,0,0,.2)}

  .headline{position:absolute;left:27px;top:38px;font-family:"Caveat Brush",cursive;font-size:42px;line-height:1;color:var(--ink-light);letter-spacing:.5px}
  .message{position:absolute;left:33px;top:83px;width:310px;font-family:"Crimson Text",serif;font-size:11.4px;line-height:13.7px;color:var(--ink-light)}
  .signature{position:absolute;left:33px;top:178px;font-family:"Crimson Text",serif;font-size:11.4px;color:var(--ink-light)}
</style>
</head>
<body>
<div class="canvas">

  <section class="spread spread--outside">
    <div class="panel panel--back">
      <figure class="photo photo--cover">
        <div class="photo__image" role="img" aria-label="Foto: schlafendes Neugeborenes auf heller Decke"></div>
      </figure>
    </div>
    <div class="fold"></div>
    <div class="panel panel--front">
      <svg class="badge" viewBox="0 0 380 254" aria-hidden="false">
        <defs>
          <linearGradient id="portrait-tone" x1="0" y1="0" x2="1" y2="1">
            <stop offset="0" stop-color="#eee9e4"/>
            <stop offset="1" stop-color="#e2c9b8"/>
          </linearGradient>
        </defs>
        <rect x="0" y="112" width="380" height="36" fill="var(--teal-dark)"/>
        <line x1="4" y1="118" x2="376" y2="118" stroke="#fff" stroke-width="2" stroke-dasharray="2 5"/>
        <line x1="4" y1="142" x2="376" y2="142" stroke="#fff" stroke-width="2" stroke-dasharray="2 5"/>
        <g transform="translate(55 0)">
          <path fill="var(--teal-dark)" d="M45,18 Q135,-8 225,18 A27 27 0 0 0 252,45 L252,209 A27 27 0 0 0 225,236 Q135,262 45,236 A27 27 0 0 0 18,209 L18,45 A27 27 0 0 0 45,18 Z"/>
          <path role="img" aria-label="Foto: Porträt des Babys auf weißem Kissen" fill="url(#portrait-tone)" transform="translate(135 127) scale(0.9) translate(-135 -127)" d="M45,18 Q135,-8 225,18 A27 27 0 0 0 252,45 L252,209 A27 27 0 0 0 225,236 Q135,262 45,236 A27 27 0 0 0 18,209 L18,45 A27 27 0 0 0 45,18 Z"/>
        </g>
      </svg>
      <h1 class="name">Theo</h1>
      <p class="facts">14.06.2016 · 14.15 Uhr<br>3000 Gramm · 50 cm</p>
    </div>
  </section>

  <section class="spread spread--inside">
    <div class="panel panel--inside">
      <h2 class="headline">Theo ist endlich da!</h2>
      <p class="message">Lorem ipsum dolor sit amet, consectetuer adipiscing elit. Aenean commodo ligula eget dolor. Aenean massa. Cum sociis natoque penatibus et magnis dis parturient montes, nascetur ridiculus mus. Donec quam felis, ultricies nec, pellentesque eu,</p>
      <p class="signature">Anna &amp; Bernd Mustermann</p>
      <figure class="photo photo--inside-left">
        <div class="photo__image" role="img" aria-label="Foto: schlafendes Baby mit Armen über dem Kopf auf Fell"></div>
      </figure>
      <figure class="photo photo--inside-top">
        <div class="photo__image" role="img" aria-label="Foto: Babyhand hält den Finger eines Erwachsenen"></div>
      </figure>
      <figure class="photo photo--inside-bottom">
        <div class="photo__image" role="img" aria-label="Foto: Neugeborenes im Profil, Kopf in einer Hand gehalten"></div>
      </figure>
    </div>
    <div class="fold fold--inside"></div>
  </section>

</div>
</body>
</html>
```